Business card for Luxury Portable Restroom Trailer company

We are a Luxury Portable Restroom Trailer Company Called FALCRIDGE HIRES. Based in Orange County California. We provide portable restroom trailers for events, such as, Weddings, Concerts, Charity events, Sporting events, Tournaments, Corporate events, ect. We rent and Sell the Luxury restrooms. Our colors are white, grey, and Orange. As you will see in the logo we uploaded.
There are 2 people in the company so the names and titles will change for the 3 people but card will remain the same. Here is the information for each Person: Dwight Penner CFO 555 318-0476
next Person: Leon Marchetti VP 555 318-0476
Next Person: Owen Marchetti CEO 555 318-0476
Information to include on the card: Luxury Restroom Trailers Rental and Sales. Weddings, Concerts, Charity, Sporting and Corp. Events.

```html
<!DOCTYPE html>
<html lang="en">
<head>
<meta charset="utf-8">
<title>Falcridge Hires – Business Card</title>
<link href="https://fonts.googleapis.com/css2?family=Archivo:wght@400;500;700&display=swap" rel="stylesheet">
<style>
  :root {
    --bg: #e4e4e6;
    --card-white: #ffffff;
    --card-grey: #4a4a4d;
    --orange: #e8641e;
    --text-light: #f4f4f4;
    --text-dark: #3d3d40;
  }
  * { box-sizing: border-box; margin: 0; padding: 0; }
  html, body { width: 1200px; height: 800px; overflow: hidden; }
  body {
    background: var(--bg);
    font-family: "Archivo", Arial, sans-serif;
    display: flex;
    flex-direction: column;
    align-items: center;
    justify-content: center;
    gap: 40px;
  }
  .card {
    position: relative;
    width: 600px;
    height: 343px;
    border-radius: 18px;
    overflow: hidden;
    box-shadow: 0 10px 28px rgba(0,0,0,0.18);
  }
  .card-bg { position: absolute; inset: 0; }

  /* Brand name */
  .brand {
    display: flex;
    align-items: center;
    gap: 10px;
    font-weight: 700;
    letter-spacing: 0.04em;
    text-transform: uppercase;
    white-space: nowrap;
  }
  .brand-mark { display: block; flex: none; background: var(--orange); }

  /* Front */
  .card-front { background: var(--card-white); }
  .card-front .brand {
    position: absolute;
    left: 34px;
    top: 118px;
    font-size: 19px;
    line-height: 23px;
    color: var(--text-dark);
  }
  .card-front .brand-mark { width: 14px; height: 14px; }

  .contact {
    position: absolute;
    right: 34px;
    top: 44px;
    text-align: right;
    color: var(--text-light);
  }
  .contact-name {
    color: var(--orange);
    font-weight: 700;
    font-size: 22px;
    letter-spacing: 0.02em;
    text-transform: uppercase;
  }
  .contact-title { font-size: 13px; margin-top: 2px; margin-bottom: 22px; }
  .contact-line {
    font-size: 14px;
    line-height: 20px;
    display: flex;
    justify-content: flex-end;
    align-items: center;
    gap: 7px;
  }
  .contact-line.address { padding-right: 21px; }
  .address-block { margin-bottom: 10px; }
  .icon { width: 14px; height: 14px; flex: none; }

  /* Back */
  .card-back {
    background: var(--card-grey);
    display: flex;
    flex-direction: column;
    align-items: center;
    justify-content: center;
    color: var(--text-light);
  }
  .card-back .brand {
    font-size: 44px;
    color: var(--text-light);
    margin-bottom: 38px;
  }
  .card-back .brand-mark { width: 26px; height: 26px; }
  .tagline { font-size: 17px; line-height: 26px; text-align: center; }
</style>
</head>
<body>

  <section class="card card-front">
    <svg class="card-bg" viewBox="0 0 600 343" preserveAspectRatio="none" aria-hidden="true">
      <path d="M318 0 C262 0 262 120 206 196 C158 262 80 290 0 292 L0 343 L600 343 L600 0 Z" fill="#e8641e"/>
      <path d="M334 0 C276 0 278 124 222 202 C172 270 88 300 0 304 L0 343 L600 343 L600 0 Z" fill="#4a4a4d"/>
    </svg>

    <div class="brand"><span class="brand-mark"></span><span class="brand-name">Falcridge<br>Hires</span></div>

    <div class="contact">
      <p class="contact-name">Dwight Penner</p>
      <p class="contact-title">CFO</p>
      <div class="address-block">
        <p class="contact-line address">2170 Harbor Crest Drive</p>
        <p class="contact-line address">Tustin, CA 92780</p>
      </div>
      <p class="contact-line">555 318-0476
        <svg class="icon" viewBox="0 0 14 14" aria-hidden="true"><path d="M3 1.5 L5.2 1.5 L6 4.4 L4.6 5.5 C5.3 7 6.8 8.6 8.4 9.4 L9.6 8 L12.5 8.8 L12.5 11 C12.5 11.9 11.8 12.5 10.9 12.5 C5.6 12.1 1.9 8.4 1.5 3.1 C1.5 2.2 2.1 1.5 3 1.5 Z" fill="#e8641e"/></svg>
      </p>
      <p class="contact-line">name@FALCRIDGE.com
        <svg class="icon" viewBox="0 0 14 14" aria-hidden="true"><rect x="1" y="3" width="12" height="8.5" rx="1" fill="#e8641e"/><path d="M1.5 3.6 L7 8 L12.5 3.6" fill="none" stroke="#4a4a4d" stroke-width="1.2"/></svg>
      </p>
      <p class="contact-line">www.FALCRIDGE.com
        <svg class="icon" viewBox="0 0 14 14" aria-hidden="true"><circle cx="7" cy="7" r="6" fill="#e8641e"/><path d="M1 7 H13 M7 1 C4.5 4 4.5 10 7 13 M7 1 C9.5 4 9.5 10 7 13" fill="none" stroke="#4a4a4d" stroke-width="1"/></svg>
      </p>
    </div>
  </section>

  <section class="card card-back">
    <div class="brand"><span class="brand-mark"></span>Falcridge Hires</div>
    <p class="tagline">Luxury Restroom Trailers Rental and Sales<br>Weddings, Concerts, Charity, Sporting and Corp Events</p>
  </section>

</body>
</html>
```